Vexa - Booking activities for Kids and Adults.

The app allows booking of Kid's activities for a given date/time.
The app lists activities offered via various clubs (vendors) which a user can book for their kids.
The users can browse various clubs and their offered activities. The users can manage their kid's profiles.
Need a whole new look to the app. The existing app can be checked out at
https://apps.storefrontexample.test/details?id=com.vexakw
https://apps.appmarketexample.test/us/app/vexa-فيكسا/id7302958146?ls=1
Try using the app as Guest.

Target Market(s)

Kuwait

Font styles to use
Serif
Sans Serif

Requirements
Must have
• Home Screens
The home page should have everything from the existing app and a quick area to change between different kid's profile to see activities matching their interests ONLY. In the current version, there's no switch profile and hence we are showing the name tags on the activities.

We are also going to build ecommerce so we need that ecommerce look and feel.
Kindly maintain the image aspect ratio from the current app so the new version doesn't require new images.

Need a complete new innovative designs - Keep the color scheme same.
The designs should be minimalistic and image oriented. The design should be done in XD. The designs should be submitted in both light and dark theme.
Reference to be used - http://plimtor.example

D.M for more info if needed.

```html
<!DOCTYPE html>
<html lang="en">
<head>
<meta charset="utf-8">
<title>Vexa – Schedule</title>
<link rel="stylesheet" href="https://fonts.googleapis.com/css2?family=Poppins:wght@400;500;600;700;800&display=swap">
<style>
  :root {
    --teal: #43c2c1;
    --teal-soft: rgba(255,255,255,0.22);
    --orange: #f7941d;
    --white: #ffffff;
    --page: #f8f8f8;
    --sheet: #efefef;
    --ink: #2b2b2b;
    --muted: #7b7b7b;
    --pill: #f3f3f3;
    --line: #d9d9d9;
    --cancel: #fe6262;
    --cancel-edge: #c94a4a;
  }
  * { box-sizing: border-box; margin: 0; padding: 0; }
  html, body { width: 1200px; height: 2592px; overflow: hidden; }
  body { font-family: "Poppins", sans-serif; background: var(--page); color: var(--ink); }
  .screen { position: relative; width: 1200px; height: 2592px; overflow: hidden; background: var(--page); }

  .teal-band { position: absolute; left: 0; top: 0; width: 1200px; height: 1177px; background: var(--teal); }

  .app-header { position: absolute; left: 0; top: 0; width: 1200px; height: 370px; background: var(--white); border-radius: 0 0 130px 130px; }
  .status-time { position: absolute; left: 97px; top: 32px; font-size: 46px; font-weight: 500; color: #111; }
  .status-icons { position: absolute; right: 66px; top: 44px; }
  .menu-icon { position: absolute; left: 67px; top: 198px; }
  .brand { position: absolute; left: 0; right: 0; top: 158px; text-align: center; font-size: 110px; font-weight: 600; color: var(--orange); line-height: 1; }
  .basket-icon { position: absolute; left: 962px; top: 190px; }
  .bell-icon { position: absolute; left: 1066px; top: 190px; }

  .back-btn { position: absolute; left: 64px; top: 440px; }
  .page-title { position: absolute; left: 0; right: 0; top: 436px; text-align: center; font-size: 66px; font-weight: 700; color: var(--white); }
  .calendar-btn { position: absolute; left: 1068px; top: 446px; }

  .date-badge { position: absolute; left: 80px; top: 609px; width: 334px; height: 334px; border-radius: 50%; background: var(--orange); border: 9px solid var(--white); color: var(--white); text-align: center; }
  .date-badge .day { display: block; font-size: 136px; font-weight: 800; line-height: 1; margin-top: 78px; }
  .date-badge .month { display: block; font-size: 37px; font-weight: 600; margin-top: 8px; }

  .month-grid { position: absolute; left: 491px; top: 568px; width: 658px; display: grid; grid-template-columns: repeat(7, 94px); grid-auto-rows: 68.5px; color: var(--white); text-align: center; }
  .month-grid .weekday { font-size: 24px; font-weight: 600; line-height: 56px; height: 56px; }
  .month-grid .weekday-row { display: contents; }
  .month-grid .date { position: relative; font-size: 28px; font-weight: 400; display: flex; align-items: center; justify-content: center; }
  .month-grid .date.has-event::before,
  .month-grid .date.today::before { content: ""; position: absolute; width: 64px; height: 64px; border-radius: 50%; left: 50%; top: 50%; transform: translate(-50%, -50%); background: var(--teal-soft); z-index: 0; }
  .month-grid .date.today::before { background: var(--white); }
  .month-grid .date.today { color: var(--ink); }
  .month-grid .date span { position: relative; z-index: 1; }
  .grid-header { display: contents; }

  .session-list { position: absolute; left: 68px; top: 1075px; width: 1063px; }
  .session-card { position: relative; height: 194px; margin-bottom: 33px; background: var(--white); border-radius: 27px; box-shadow: 0 8px 22px rgba(0,0,0,0.08); }
  .session-card::before { content: ""; position: absolute; left: 0; top: 60px; width: 10px; height: 74px; background: var(--orange); border-radius: 0 3px 3px 0; }
  .time-pill { position: absolute; left: 58px; top: 33px; width: 227px; height: 128px; border-radius: 22px; background: var(--pill); display: flex; align-items: center; padding-left: 38px; gap: 14px; }
  .time-pill .times { font-size: 23px; font-weight: 700; line-height: 1.3; color: var(--ink); }
  .session-title { position: absolute; left: 328px; top: 42px; font-size: 37px; font-weight: 700; color: var(--ink); }
  .session-kids { position: absolute; left: 328px; top: 100px; font-size: 32px; color: var(--muted); display: flex; align-items: center; gap: 10px; }
  .more-btn { position: absolute; left: 899px; top: 50px; }

  .action-sheet { position: absolute; left: 0; top: 1834px; width: 1200px; height: 800px; background: var(--sheet); border-radius: 100px 100px 0 0; }
  .action-list { list-style: none; position: absolute; left: 67px; top: 0; width: 1065px; }
  .action-item { height: 133px; display: flex; align-items: center; justify-content: center; gap: 18px; font-size: 40px; color: var(--ink); border-bottom: 2px solid var(--line); }
  .action-item:first-child { height: 132px; }
  .action-item:last-child { border-bottom: none; }
  .cancel-btn { position: absolute; left: 67px; top: 545px; width: 1064px; height: 117px; border-radius: 58px; background: var(--cancel); box-shadow: 0 5px 0 var(--cancel-edge); color: var(--white); font-size: 50px; font-weight: 700; display: flex; align-items: center; justify-content: center; letter-spacing: 1px; }
</style>
</head>
<body>
<div class="screen">
  <div class="teal-band"></div>

  <header class="app-header">
    <div class="status-time">11:04</div>
    <svg class="status-icons" width="185" height="32" viewBox="0 0 185 32">
      <rect x="0" y="20" width="7" height="10" rx="1.5" fill="#111"/>
      <rect x="10" y="15" width="7" height="15" rx="1.5" fill="#111"/>
      <rect x="20" y="9" width="7" height="21" rx="1.5" fill="#111"/>
      <rect x="30" y="3" width="7" height="27" rx="1.5" fill="#bbb"/>
      <path d="M64 12 a24 24 0 0 1 34 0" stroke="#111" stroke-width="5" fill="none" stroke-linecap="round"/>
      <path d="M70 19 a15 15 0 0 1 22 0" stroke="#111" stroke-width="5" fill="none" stroke-linecap="round"/>
      <circle cx="81" cy="27" r="4" fill="#111"/>
      <rect x="123" y="4" width="52" height="25" rx="7" fill="none" stroke="#111" stroke-width="2.5"/>
      <rect x="127" y="8" width="44" height="17" rx="4" fill="#111"/>
      <rect x="177" y="12" width="4" height="9" rx="2" fill="#111"/>
    </svg>
    <svg class="menu-icon" width="72" height="60" viewBox="0 0 72 60">
      <g stroke="#2b2b2b" stroke-width="6" stroke-linecap="round">
        <line x1="3" y1="5" x2="66" y2="5"/>
        <line x1="12" y1="30" x2="66" y2="30"/>
        <line x1="22" y1="55" x2="66" y2="55"/>
      </g>
    </svg>
    <div class="brand">Vexa</div>
    <svg class="basket-icon" width="74" height="72" viewBox="0 0 74 72">
      <g stroke="#2b2b2b" stroke-width="4" fill="none" stroke-linejoin="round">
        <path d="M22 28 L37 12 L52 28"/>
        <path d="M5 28 H69 V36 H5 Z"/>
        <path d="M10 36 L15 66 H59 L64 36"/>
        <line x1="27" y1="44" x2="27" y2="58"/>
        <line x1="37" y1="44" x2="37" y2="58"/>
        <line x1="47" y1="44" x2="47" y2="58"/>
      </g>
      <circle cx="37" cy="9" r="8" fill="var(--orange)"/>
    </svg>
    <svg class="bell-icon" width="68" height="76" viewBox="0 0 68 76">
      <g stroke="#2b2b2b" stroke-width="4" fill="none" stroke-linejoin="round">
        <path d="M10 58 C16 50 14 42 15 32 C16 20 24 13 34 13 C44 13 52 20 53 32 C54 42 52 50 58 58 Z"/>
        <path d="M27 64 a7 7 0 0 0 14 0"/>
      </g>
      <circle cx="34" cy="8" r="7" fill="var(--orange)"/>
    </svg>
  </header>

  <svg class="back-btn" width="30" height="44" viewBox="0 0 30 44">
    <path d="M22 8 L9 22 L22 36" stroke="#fff" stroke-width="6" fill="none" stroke-linecap="round" stroke-linejoin="round"/>
  </svg>
  <h1 class="page-title">Schedule</h1>
  <svg class="calendar-btn" width="64" height="66" viewBox="0 0 64 66">
    <rect x="3" y="8" width="58" height="55" rx="6" fill="none" stroke="#fff" stroke-width="4"/>
    <rect x="3" y="8" width="58" height="13" rx="5" fill="#fff"/>
    <rect x="15" y="2" width="5" height="12" rx="2" fill="#fff"/>
    <rect x="44" y="2" width="5" height="12" rx="2" fill="#fff"/>
    <g fill="#fff">
      <rect x="11" y="28" width="9" height="7"/><rect x="23" y="28" width="9" height="7"/><rect x="35" y="28" width="9" height="7"/><rect x="47" y="28" width="7" height="7"/>
      <rect x="11" y="38" width="9" height="7"/><rect x="23" y="38" width="9" height="7"/><rect x="35" y="38" width="9" height="7"/><rect x="47" y="38" width="7" height="7"/>
      <rect x="11" y="48" width="9" height="7"/><rect x="23" y="48" width="9" height="7"/><rect x="35" y="48" width="9" height="7"/>
    </g>
  </svg>

  <div class="date-badge">
    <span class="day">10</span>
    <span class="month">MARCH</span>
  </div>

  <div class="month-grid">
    <div class="weekday">SUN</div><div class="weekday">MON</div><div class="weekday">TUE</div><div class="weekday">WED</div><div class="weekday">THU</div><div class="weekday">FRI</div><div class="weekday">SAT</div>
    <div class="date"><span>30</span></div><div class="date"><span>1</span></div><div class="date"><span>2</span></div><div class="date"><span>3</span></div><div class="date"><span>4</span></div><div class="date"><span>5</span></div><div class="date"><span>6</span></div>
    <div class="date"><span>7</span></div><div class="date"><span>8</span></div><div class="date"><span>9</span></div><div class="date today"><span>10</span></div><div class="date"><span>11</span></div><div class="date has-event"><span>12</span></div><div class="date"><span>13</span></div>
    <div class="date has-event"><span>14</span></div><div class="date"><span>15</span></div><div class="date"><span>16</span></div><div class="date"><span>17</span></div><div class="date"><span>18</span></div><div class="date"><span>19</span></div><div class="date"><span>20</span></div>
    <div class="date"><span>21</span></div><div class="date"><span>22</span></div><div class="date has-event"><span>23</span></div><div class="date"><span>24</span></div><div class="date"><span>25</span></div><div class="date"><span>26</span></div><div class="date"><span>27</span></div>
    <div class="date"><span>28</span></div><div class="date"><span>29</span></div><div class="date"><span>30</span></div><div class="date"><span>31</span></div><div class="date"><span>1</span></div><div class="date"><span>2</span></div><div class="date"><span>3</span></div>
  </div>

  <section class="session-list">
    <article class="session-card">
      <div class="time-pill">
        <svg width="26" height="26" viewBox="0 0 26 26"><circle cx="13" cy="13" r="13" fill="#9a9a9a"/><path d="M13 6 V14 H18" stroke="#fff" stroke-width="2.5" fill="none"/></svg>
        <div class="times">11:00 AM<br>01:00 PM</div>
      </div>
      <h2 class="session-title">Reading for Tots</h2>
      <p class="session-kids"><svg width="22" height="26" viewBox="0 0 22 26"><circle cx="11" cy="7" r="6" fill="#c9c9c9"/><path d="M0 26 C0 17 22 17 22 26 Z" fill="#c9c9c9"/></svg>Hala, Sami</p>
      <svg class="more-btn" width="96" height="96" viewBox="0 0 96 96"><circle cx="48" cy="48" r="46" fill="none" stroke="#d8d8d8" stroke-width="2.5" stroke-dasharray="6 5"/><circle cx="33" cy="48" r="6" fill="#d0d0d0"/><circle cx="48" cy="48" r="6" fill="#d0d0d0"/><circle cx="63" cy="48" r="6" fill="#d0d0d0"/></svg>
    </article>
    <article class="session-card">
      <div class="time-pill">
        <svg width="26" height="26" viewBox="0 0 26 26"><circle cx="13" cy="13" r="13" fill="#9a9a9a"/><path d="M13 6 V14 H18" stroke="#fff" stroke-width="2.5" fill="none"/></svg>
        <div class="times">11:00 AM<br>01:00 PM</div>
      </div>
      <h2 class="session-title">Swimming for begginers</h2>
      <p class="session-kids"><svg width="22" height="26" viewBox="0 0 22 26"><circle cx="11" cy="7" r="6" fill="#c9c9c9"/><path d="M0 26 C0 17 22 17 22 26 Z" fill="#c9c9c9"/></svg>Hala, Sami</p>
      <svg class="more-btn" width="96" height="96" viewBox="0 0 96 96"><circle cx="48" cy="48" r="46" fill="none" stroke="#d8d8d8" stroke-width="2.5" stroke-dasharray="6 5"/><circle cx="33" cy="48" r="6" fill="#d0d0d0"/><circle cx="48" cy="48" r="6" fill="#d0d0d0"/><circle cx="63" cy="48" r="6" fill="#d0d0d0"/></svg>
    </article>
    <article class="session-card">
      <div class="time-pill">
        <svg width="26" height="26" viewBox="0 0 26 26"><circle cx="13" cy="13" r="13" fill="#9a9a9a"/><path d="M13 6 V14 H18" stroke="#fff" stroke-width="2.5" fill="none"/></svg>
        <div class="times">11:00 AM<br>01:00 PM</div>
      </div>
      <h2 class="session-title">Swimming level 2</h2>
      <p class="session-kids"><svg width="22" height="26" viewBox="0 0 22 26"><circle cx="11" cy="7" r="6" fill="#c9c9c9"/><path d="M0 26 C0 17 22 17 22 26 Z" fill="#c9c9c9"/></svg>Hala, Sami</p>
      <svg class="more-btn" width="96" height="96" viewBox="0 0 96 96"><circle cx="48" cy="48" r="46" fill="none" stroke="#d8d8d8" stroke-width="2.5" stroke-dasharray="6 5"/><circle cx="33" cy="48" r="6" fill="#d0d0d0"/><circle cx="48" cy="48" r="6" fill="#d0d0d0"/><circle cx="63" cy="48" r="6" fill="#d0d0d0"/></svg>
    </article>
  </section>

  <section class="action-sheet">
    <ul class="action-list">
      <li class="action-item">
        <svg width="54" height="54" viewBox="0 0 54 54"><g stroke="#2b2b2b" stroke-width="3"><line x1="12" y1="27" x2="42" y2="10"/><line x1="12" y1="27" x2="42" y2="44"/></g><circle cx="12" cy="27" r="7" fill="var(--teal)" stroke="#2b2b2b" stroke-width="3"/><circle cx="42" cy="10" r="7" fill="var(--teal)" stroke="#2b2b2b" stroke-width="3"/><circle cx="42" cy="44" r="7" fill="var(--teal)" stroke="#2b2b2b" stroke-width="3"/></svg>
        Share
      </li>
      <li class="action-item">
        <svg width="64" height="56" viewBox="0 0 64 56"><path d="M4 18 C4 6 60 6 60 18 L60 22 L46 22 L46 16 L18 16 L18 22 L4 22 Z" fill="var(--teal)" stroke="#2b2b2b" stroke-width="3" stroke-linejoin="round"/><path d="M14 30 L20 22 H44 L50 30 V52 H14 Z" fill="none" stroke="#2b2b2b" stroke-width="3" stroke-linejoin="round"/><circle cx="32" cy="37" r="7" fill="none" stroke="#2b2b2b" stroke-width="3"/></svg>
        Call
      </li>
      <li class="action-item">
        <svg width="60" height="60" viewBox="0 0 60 60"><rect x="4" y="8" width="52" height="48" rx="6" fill="none" stroke="#2b2b2b" stroke-width="3"/><line x1="4" y1="20" x2="56" y2="20" stroke="#2b2b2b" stroke-width="3"/><line x1="17" y1="3" x2="17" y2="13" stroke="#2b2b2b" stroke-width="3"/><line x1="43" y1="3" x2="43" y2="13" stroke="#2b2b2b" stroke-width="3"/><g fill="var(--teal)" stroke="#2b2b2b" stroke-width="2"><rect x="13" y="27" width="8" height="7"/><rect x="26" y="27" width="8" height="7"/><rect x="39" y="27" width="8" height="7"/><rect x="13" y="40" width="8" height="7"/><rect x="26" y="40" width="8" height="7"/><rect x="39" y="40" width="8" height="7"/></g></svg>
        Add to calendar
      </li>
      <li class="action-item">
        <svg width="60" height="62" viewBox="0 0 60 62"><path d="M6 6 H48 L56 13 L48 20 H6 Z" fill="var(--teal)" stroke="#2b2b2b" stroke-width="3" stroke-linejoin="round"/><path d="M54 24 H12 L4 31 L12 38 H54 Z" fill="#fff" stroke="#2b2b2b" stroke-width="3" stroke-linejoin="round"/><line x1="30" y1="2" x2="30" y2="6" stroke="#2b2b2b" stroke-width="3"/><line x1="30" y1="20" x2="30" y2="24" stroke="#2b2b2b" stroke-width="3"/><line x1="30" y1="38" x2="30" y2="60" stroke="#2b2b2b" stroke-width="3"/></svg>
        Directions
      </li>
    </ul>
    <div class="cancel-btn">CANCEL</div>
  </section>
</div>
</body>
</html>
```